K & R Acre Works. Business card design

We need a business card designed for a new business. We have a bulldozer and tractor service. We clear land and make wildlife food plots. We provide disking, bush hogging, and site prep services.
I have attached an image of a business card that I like and would like my business cards to look similar.

Target Market(s)

anyone needing bulldozer and/or tractor services

Industry/Entity Type

Business

Contact Information for Business Card

K & R Acre Works, Operated by 7-T-Ranch
Wade Colton
601-472-3358
wcr4817@fieldmail-example.com

Font styles to use
Sans Serif

Colors

Designer to choose colors to be used in the design.

Requirements
Must have
• image of tractor and bulldozer
• Land Clearing
• Wildlife food plots
• Bush Hogging
• Disking
• Site prep
Nice to have
• i have included a image of a business card that i like. I would like mine to be similar.

```html
<!DOCTYPE html>
<html lang="en">
<head>
<meta charset="utf-8">
<title>K &amp; R Acre Works – Business Card</title>
<link href="https://fonts.googleapis.com/css2?family=Roboto:wght@400;500;700&family=Roboto+Condensed:wght@700&display=swap" rel="stylesheet">
<style>
  :root {
    --backdrop: #2e2e2e;
    --card: #f4f4f2;
    --olive: #8f8a2e;
    --brown: #6b3f1c;
    --rule: #9a5f2a;
    --ink: #3e3e3e;
    --dozer-tone-a: #6f7560;
    --dozer-tone-b: #8a7a56;
    --tractor-tone-a: #7e8a4a;
    --tractor-tone-b: #b2552e;
  }
  * { margin: 0; padding: 0; box-sizing: border-box; }
  html, body {
    width: 1200px; height: 960px; overflow: hidden;
    background: var(--backdrop);
    font-family: "Roboto", Arial, sans-serif;
  }
  .business-card {
    position: absolute; left: 300px; top: 309px;
    width: 600px; height: 343px;
    background: var(--card);
  }
  .brand {
    position: absolute; right: 30px; top: 33px;
    text-align: right;
  }
  .brand-name {
    display: block;
    font-family: "Roboto Condensed", "Arial Narrow", sans-serif;
    font-weight: 700; font-size: 21px; line-height: 22px;
    color: var(--brown); letter-spacing: 0.3px;
  }
  .brand-tagline {
    display: block; margin-top: 2px;
    font-family: "Roboto Condensed", "Arial Narrow", sans-serif;
    font-weight: 700; font-size: 10.5px; color: #3a3a3a;
    letter-spacing: 0.2px;
  }
  .equipment-photo { position: absolute; top: 71px; height: 80px; }
  .photo-dozer {
    left: 323px; width: 134px;
    background: linear-gradient(160deg, #7d8d6a 0%, var(--dozer-tone-a) 45%, var(--dozer-tone-b) 100%);
  }
  .photo-tractor {
    left: 462px; width: 108px;
    background: linear-gradient(160deg, #8f9a52 0%, var(--tractor-tone-a) 40%, var(--tractor-tone-b) 70%, #8a8050 100%);
  }
  .contact-block { position: absolute; left: 29px; top: 180px; width: 538px; }
  .person-name {
    font-size: 21px; font-weight: 500; color: var(--olive);
    line-height: 26px; letter-spacing: -0.2px;
  }
  .person-role {
    font-size: 14px; font-weight: 500; color: var(--brown);
    line-height: 18px;
  }
  .divider { height: 1.5px; background: var(--rule); margin: 6px 0 7px 2px; }
  .services-heading {
    font-size: 16px; font-weight: 700; color: var(--olive); line-height: 20px;
  }
  .service-list { list-style: none; margin-top: 2px; }
  .service-list li {
    font-size: 14px; color: var(--ink); line-height: 18px;
  }
  .dot { color: var(--olive); font-size: 11px; padding: 0 3px 0 1px; vertical-align: 1px; }
  .contact-line {
    margin-top: 5px; font-size: 14px; color: var(--ink); line-height: 18px;
  }
  .contact-line .label { color: var(--olive); font-weight: 700; }
</style>
</head>
<body>
  <section class="business-card">
    <div class="brand">
      <span class="brand-name">K &amp; R ACRE WORKS</span>
      <span class="brand-tagline">FOR ALL OF YOUR LAND IMPROVEMENT NEEDS</span>
    </div>
    <div class="equipment-photo photo-dozer" role="img" aria-label="Photo of a yellow bulldozer pushing a pile of soil"></div>
    <div class="equipment-photo photo-tractor" role="img" aria-label="Photo of an orange tractor with a front loader in a field"></div>

    <div class="contact-block">
      <h1 class="person-name">WADE COLTON</h1>
      <p class="person-role">OWNER</p>
      <div class="divider"></div>
      <h2 class="services-heading">WE CREADED</h2>
      <ul class="service-list">
        <li><span class="dot">●</span>Land Clearing <span class="dot">●</span>Wildlife food plots</li>
        <li><span class="dot">●</span>Bush Hogging<span class="dot">●</span>Disking <span class="dot">●</span>Site prep</li>
      </ul>
      <p class="contact-line">
        <span class="label">P.</span> 601-472-3358
        <span class="label">E.</span>&nbsp; wcr4817@fieldmail-example.com
        <span class="label">W.</span>&nbsp; kracreworks-example.com
      </p>
    </div>
  </section>
</body>
</html>
```